Brookvale Estates LLC stationary for a real estate property management company.

Create stationary (letterhead, envelopes, business cards) using Brookvale Estates LLC logo as primary creative element. Stationary design needs to be horizontal, leaving as much space as possible for correspondence copy. See attached Creative Brief and past stationary files for details.

Target Market(s)

Prospective apartment residents and current residents, vendors, and government agencies.

Industry/Entity Type

Property Management

Contact Information for Business Card

Business card employee title: Property Manager. Should include address, phone, fax, email, website, slogan, and Brookvale Estates logo.

Font styles to use
Sans Serif

Colors
0592cd
000000

Requirements
Must have
• Tone should be conservative, institutional, business (i.e. banking, finance, real estate). Must include: address, phone, fax, website, and slogan (see attached Creative Brief). Should be a horizontal design, leaving as much room as possible for letter correspondence copy.
Nice to have
• Please use an Arial or Helvetica style font.
Should not have
• Letterhead layout should leave as much room as possible for copy.

```html
<!DOCTYPE html>
<html lang="en">
<head>
<meta charset="utf-8">
<title>Brookvale Estates LLC – Stationery</title>
<link rel="stylesheet" href="https://fonts.googleapis.com/css2?family=Arimo:wght@400;700&family=Open+Sans:wght@400&display=swap">
<style>
  :root{
    --brand-blue:#0b6aab;
    --brand-blue-bright:#0592cd;
    --ink:#000000;
    --text:#333333;
    --muted:#4a4a4a;
    --paper:#f5f5f5;
    --backdrop:#cbc2b6;
    --shadow:0 2px 6px rgba(0,0,0,.28);
  }
  *{margin:0;padding:0;box-sizing:border-box}
  html,body{width:1200px;height:754px;overflow:hidden}
  body{background:var(--backdrop);position:relative;font-family:"Arimo",Arial,sans-serif;color:var(--text)}

  .brand{display:flex;align-items:center;gap:6px;color:var(--brand-blue);font-family:"Arimo",Arial,sans-serif;font-weight:700;white-space:nowrap}
  .brand__square{width:14px;height:14px;background:var(--brand-blue);flex:none}

  /* Letterhead */
  .letterhead{position:absolute;left:36px;top:32px;width:489px;height:689px;background:var(--paper);box-shadow:var(--shadow)}
  .letterhead .brand{position:absolute;left:47px;top:67px;font-size:18px}
  .letterhead__contact{position:absolute;right:47px;top:45px;text-align:right;font-size:8px;line-height:10.2px;color:var(--muted)}
  .letterhead__contact .row{display:flex;justify-content:flex-end;align-items:center;gap:4px}
  .letterhead__contact .spacer{height:4px}
  .icon{width:7px;height:7px;fill:var(--brand-blue)}
  .letter{position:absolute;left:49px;top:193px;width:394px;font-family:"Open Sans",Arial,sans-serif;color:var(--muted)}
  .letter__greeting{font-size:13px;margin-bottom:20px}
  .letter__body p{font-size:7.1px;line-height:11.8px;margin-bottom:11.8px;text-align:justify}
  .letter__closing{font-size:7.1px;margin-top:22px}
  .letter__signature{display:block;width:62px;height:22px;margin-top:8px;background:linear-gradient(90deg,rgba(30,30,40,.55),rgba(30,30,40,.25));border-radius:2px}

  /* Business card */
  .card{position:absolute;left:716px;top:106px;width:313px;height:178px;background:linear-gradient(120deg,#1f4f86 0%,#6b8fb2 28%,#d9dee3 55%,#eceff1 100%);box-shadow:var(--shadow);text-align:right;color:var(--ink);font-family:"Arimo",Arial,sans-serif}
  .card__inner{position:absolute;right:14px;top:20px}
  .card .brand{justify-content:flex-end;font-size:18px;color:#0d2f55}
  .card .brand__square{background:#0d2f55}
  .card__name{font-weight:700;font-size:11.5px;color:#0d2f55;margin-top:14px}
  .card__title{font-size:8.5px;margin-top:1px}
  .card__lines{font-size:7.4px;line-height:9.8px;margin-top:4px}
  .card__lines .gap{height:4px}
  .card__slogan{font-weight:700;font-size:7.6px;color:#0d2f55;margin-top:5px}

  /* Envelope back */
  .envelope-back{position:absolute;left:615px;top:350px;width:549px;height:248px;background:#ececec;box-shadow:var(--shadow)}
  .envelope-back__flap{position:absolute;left:0;top:0;width:549px;height:92px}
  .envelope-back__brand{position:absolute;left:0;top:24px;width:549px;display:flex;flex-direction:column;align-items:center;gap:8px}
  .envelope-back .brand{color:#ffffff;font-size:12px}
  .envelope-back .brand__square{background:#ffffff;width:10px;height:10px}
  .envelope-back__url{color:#ffffff;font-size:7.5px}

  /* Envelope front */
  .envelope-front{position:absolute;left:547px;top:471px;width:550px;height:250px;background:var(--paper);box-shadow:var(--shadow)}
  .envelope-front .brand{position:absolute;left:23px;top:36px;font-size:17px}
  .envelope-front__address{position:absolute;left:38px;top:68px;font-size:7.8px;line-height:9.4px;color:var(--muted)}
</style>
</head>
<body>

<section class="letterhead">
  <div class="brand"><span class="brand__square"></span>Brookvale Estates LLC</div>
  <div class="letterhead__contact">
    <div>2718 Harbor Crest Drive #B210</div>
    <div>Fresno, CA 93710</div>
    <div class="spacer"></div>
    <div class="row">559-430-2716 <svg class="icon" viewBox="0 0 10 10"><path d="M2 0.5l2 2.2-1 1.2c.7 1.4 1.7 2.4 3.1 3.1l1.2-1 2.2 2-1.2 1.6C4.6 9.4.6 5.4.5 1.7z"/></svg></div>
    <div class="row">559-430-2781 <svg class="icon" viewBox="0 0 10 10"><rect x="2.5" y="0.5" width="5" height="3"/><rect x="0.5" y="3.5" width="9" height="4.5" rx="1"/><rect x="2.5" y="7" width="5" height="2.5"/></svg></div>
    <div class="row">daniel@brookvaleestates.us <svg class="icon" viewBox="0 0 10 10"><rect x="0.5" y="2" width="9" height="6"/><path d="M0.5 2l4.5 3.5L9.5 2" fill="none" stroke="#fff" stroke-width="0.9"/></svg></div>
    <div class="row">www.brookvaleestates.us <svg class="icon" viewBox="0 0 10 10"><circle cx="5" cy="5" r="4.5"/><path d="M0.5 5h9M5 0.5c-2 2.5-2 6.5 0 9M5 0.5c2 2.5 2 6.5 0 9" fill="none" stroke="#fff" stroke-width="0.7"/></svg></div>
  </div>

  <article class="letter">
    <p class="letter__greeting">Dear Mr. Harlow,</p>
    <div class="letter__body">
      <p>Lorem ipsum dolor sit amet, consectetur adipiscing elit. Donec orci purus, luctus vitae dignissim eu, iaculis sed purus. Vivamus faucibus, ipsum nec aliquet viverra, leo mauris condimentum ligula, sit amet sagittis enim ligula quis arcu. Nam egestas tortor id nisi porttitor mattis. In tortor ante, ultricies in suscipit a, tempus non massa. Vivamus et auctor mi. Fusce vel massa nulla. Phasellus nec eros mauris, et scelerisque orci.</p>
      <p>Donec malesuada orci vitae nulla accumsan porta a id massa. Quisque accumsan iaculis magna sit amet fringilla. Maecenas consequat, magna eget tincidunt semper, odio nibh rutrum mi, id feugiat ante nisi eu risus. Vestibulum nunc orci, rhoncus a placerat in, ultricies in mi. Cras mattis varius eros, vel fringilla nisi suscipit eget. Quisque scelerisque sagittis nulla at porttitor.</p>
      <p>Sed id augue vitae urna euismod commodo aliquet a quam. Pellentesque arcu velit, cursus et malesuada ut, consequat et diam. Nullam erat sem, rhoncus id ullamcorper vitae, rhoncus et arcu. In ultricies ultricies nulla, ut rutrum nisi iaculis at. Donec eu magna a metus ornare faucibus. Fusce aliquet faucibus ultricies. Morbi semper, est id tincidunt gravida, sem arcu adipiscing lacus, ac bibendum nulla leo eu purus. Quisque nec diam sed risus consectetur a accumsan quis quis nibh. Vestibulum id purus lorem.</p>
      <p>It is a long established fact that a reader will be distracted by the readable content of a page when looking at its layout. The point of using Lorem Ipsum is that it has a more-or-less normal distribution of letters, as opposed to using 'Content here, content here', making it look like readable English. Many desktop publishing packages</p>
    </div>
    <p class="letter__closing">Sincerely,</p>
    <span class="letter__signature" role="img" aria-label="Handwritten signature"></span>
  </article>
</section>

<section class="card">
  <div class="card__inner">
    <div class="brand"><span class="brand__square"></span>Brookvale Estates LLC</div>
    <div class="card__name">DANIEL WARD</div>
    <div class="card__title">Property Manager</div>
    <div class="card__lines">
      <div>2718 Harbor Crest Drive #B210</div>
      <div>Fresno, CA 93710</div>
      <div class="gap"></div>
      <div>Phone: 559-430-2716</div>
      <div>Fax: 559-430-2781</div>
      <div>daniel@brookvaleestates.us</div>
      <div>www.brookvaleestates.us</div>
    </div>
    <div class="card__slogan">Multifamily Property Management</div>
  </div>
</section>

<section class="envelope-back">
  <svg class="envelope-back__flap" viewBox="0 0 549 92" aria-hidden="true">
    <path d="M0 0H549L534 68Q529 92 503 92H46Q20 92 15 68Z" fill="var(--brand-blue)"/>
  </svg>
  <div class="envelope-back__brand">
    <div class="brand"><span class="brand__square"></span>Brookvale Estates LLC</div>
    <div class="envelope-back__url">www.brookvaleestates.us</div>
  </div>
</section>

<section class="envelope-front">
  <div class="brand"><span class="brand__square"></span>Brookvale Estates LLC</div>
  <div class="envelope-front__address">
    <div>2718 Harbor Crest Drive #B210</div>
    <div>Fresno, CA 93710</div>
  </div>
</section>

</body>
</html>
```